Pilates business needs a face list flyer

We are a pilates business that has been based in England for 15 years and looking for a new flyer that is eye catch and modern but stylish
we are trying to capture the male market as well as the female market so the leaflet should draw attention to both groups.
I have attached a copy of the literature needed on the flyer also a picture of its founder

Target Market(s)

market age group 18-70+ male and female

Industry/Entity Type

Business

Font styles to use
Other font styles liked:
• calbri

Colors
33b8a4
34a7d8
3277b5
abd037

Requirements
Must have
• Literature attached
Nice to have
• To target both the male and female market. stylish but eye catching
Should not have
• pinks purples

```html
<!DOCTYPE html>
<html lang="en">
<head>
<meta charset="utf-8">
<title>Harwell Core Pilates – Trifold Leaflet</title>
<link href="https://fonts.googleapis.com/css2?family=Oswald:wght@300;400&family=Open+Sans:ital,wght@0,400;0,600;0,700;1,600;1,700&display=swap" rel="stylesheet">
<style>
:root{
  --teal:#33b8a4;
  --sky:#34a7d8;
  --blue:#3277b5;
  --navy:#1d4e8f;
  --lime:#abd037;
  --ink:#2b2b2b;
  --head:#2a68b0;
  --green-head:#1f8a6e;
  --paper:#ffffff;
  --mist:#eef0f1;
  --bg:#e9ebec;
}
*{box-sizing:border-box;margin:0;padding:0}
html,body{width:848px;height:1200px;overflow:hidden;background:var(--bg)}
body{font-family:"Open Sans",Arial,sans-serif;color:var(--ink);position:relative}
.sheet{position:absolute;left:29px;width:790px;height:574px;background:var(--paper);overflow:hidden;box-shadow:0 2px 8px rgba(0,0,0,.25);display:flex}
.sheet--outside{top:16px}
.sheet--inside{top:606px}
.panel{position:relative;width:263.3px;height:100%;padding:18px 18px 0}
.panel--shaded{background:linear-gradient(90deg,#f4f5f6,#e6e8ea)}
.panel--soft{background:linear-gradient(180deg,#fff 0%,#f3f4f5 100%)}
.wave{position:absolute;left:0;width:790px;pointer-events:none}
.wave--bottom{bottom:0;height:150px}
.wave--top{top:0;height:180px}
.layer{position:relative;z-index:2}

/* schedule */
.schedule{text-align:center;list-style:none;margin-top:4px}
.schedule li{margin-bottom:8.4px;line-height:1.3}
.schedule .time{display:block;color:var(--head);font-weight:700;font-size:9.6px}
.schedule .venue{display:block;font-size:8.4px}
.photo-circle{position:absolute;width:108px;height:108px;border-radius:50%;border:4px solid #fff;box-shadow:0 0 0 3px var(--blue);z-index:3}
.photo-circle--a{left:24px;top:396px;background:radial-gradient(circle at 50% 60%,#d9a989,#8fb6cf 60%,#4b86b4)}
.photo-circle--b{left:146px;top:396px;width:98px;height:98px;background:radial-gradient(circle at 50% 55%,#cf9f86,#6c7f97 55%,#2b4c78)}

/* about */
.heading{font-family:"Oswald","Arial Narrow",sans-serif;font-weight:300;color:var(--head);text-transform:uppercase;letter-spacing:.3px}
.heading--about{font-size:15px;display:flex;align-items:center;gap:12px;margin-top:6px}
.heading--about::after{content:"";flex:1;height:4px;background:var(--blue)}
.about{font-size:7.5px;line-height:1.36;text-align:justify;margin-top:8px}
.about p{margin-bottom:7px}
.portrait{float:left;width:72px;height:88px;margin:0 10px 4px 0;background:linear-gradient(160deg,#9a9a9a,#d8d8d8 55%,#5c5c5c)}
.call{font-family:"Oswald","Arial Narrow",sans-serif;font-weight:300;color:var(--head);text-align:center;font-size:22px;margin-top:4px}
.contact{text-align:center;font-size:9.2px;line-height:1.6}
.social{position:absolute;left:18px;bottom:24px;z-index:3;color:#fff;font-size:7px;display:flex;align-items:center;gap:6px;letter-spacing:.3px}
.social-square{width:12px;height:12px;background:#fff;border-radius:1px}

/* cover */
.brand{text-align:center;margin-top:12px}
.brand-mark{width:106px;height:96px;background:var(--blue);margin:0 auto 8px}
.brand-name{font-family:"Oswald","Arial Narrow",sans-serif;font-weight:300;font-size:18.5px;color:var(--ink);letter-spacing:.2px}
.brand-tag{font-size:9px;color:var(--green-head);margin-top:1px}
.cover-photo{position:absolute;left:0;right:0;top:168px;height:280px;background:radial-gradient(ellipse at 55% 45%,#d6b4a0 0%,#c9c6c0 40%,rgba(230,232,234,0) 75%)}
.cover-line{position:absolute;left:10px;right:10px;top:450px;text-align:center;font-style:italic;font-weight:700;font-size:12.6px;line-height:1.45;z-index:3}
.cover-line span{color:var(--blue)}

/* inside */
.roller-photo{position:absolute;left:0;top:0;width:263px;height:130px;background:linear-gradient(180deg,#fff 0%,#f1ece8 55%,#5b7ec9 88%,#3a5fae 100%);z-index:1}
.band-title{position:relative;z-index:3;text-align:center;color:#fff;font-family:"Oswald","Arial Narrow",sans-serif;font-weight:300}
.band-title .name{font-size:13.5px;margin-top:10px}
.band-title .phone{font-size:22px;margin-top:2px}
.body-text{font-size:7.6px;line-height:1.38;text-align:justify}
.heading--section{font-size:16px;margin:0 0 6px}
.subhead{font-weight:700;color:var(--green-head);font-size:11px;margin:10px 0 5px}
.benefits{list-style:none;font-size:7.6px;margin-top:6px}
.benefits li{position:relative;padding-left:14px;margin-bottom:5.6px;line-height:1.35}
.benefits li::before{content:"";position:absolute;left:2px;top:3px;width:4px;height:4px;border-radius:50%;background:var(--navy)}
.web{text-align:center;font-size:9.4px;margin-top:10px}
.group-photo{position:absolute;left:0;right:0;bottom:0;height:112px;background:linear-gradient(100deg,#cfc3bb,#8e8f96 45%,#cf7fa0 70%,#5c6c88);z-index:1}
.group-photo::before{content:"";position:absolute;left:0;right:0;top:0;height:18px;background:linear-gradient(180deg,#fff,rgba(255,255,255,0))}
</style>
</head>
<body>

<!-- OUTSIDE SHEET -->
<section class="sheet sheet--outside">
  <svg class="wave wave--bottom" viewBox="0 0 790 150" preserveAspectRatio="none" aria-hidden="true">
    <defs>
      <linearGradient id="seaOut" x1="0" x2="1" y1="0" y2="0">
        <stop offset="0" stop-color="#33b8a4"/>
        <stop offset=".55" stop-color="#2aa6a6"/>
        <stop offset="1" stop-color="#3277b5"/>
      </linearGradient>
    </defs>
    <path d="M0,60 C150,50 280,100 420,110 C560,118 680,90 790,55 L790,150 L0,150 Z" fill="url(#seaOut)"/>
    <path d="M0,45 C160,30 300,85 430,95 C570,104 690,70 790,30 L790,52 C690,92 570,122 430,116 C300,108 160,62 0,64 Z" fill="#abd037"/>
    <path d="M260,110 C360,122 470,128 560,124 C660,118 730,98 790,78 L790,150 L260,150 Z" fill="#1d4e8f" opacity=".85"/>
  </svg>

  <div class="panel">
    <ul class="schedule layer">
      <li><span class="time">Monday 10.30pm Beginner-Improver</span><span class="venue">The Parish Centre, Mill Rd, Oakridge</span></li>
      <li><span class="time">Monday 11.30pm Small group Class.</span><span class="venue">The Parish Centre, Mill Rd, Oakridge</span></li>
      <li><span class="time">Monday 6.45pm intermediate +</span><span class="venue">St Aidan School. The Crofts, Ashvale</span></li>
      <li><span class="time">Monday 7.45pm Beginner-Improver</span><span class="venue">St Aidan Sch, The Crofts, Ashvale</span></li>
      <li><span class="time">Tuesday 5.45pm Small group class</span><span class="venue">The Parish Centre, Elm Rd, Fenbury</span></li>
      <li><span class="time">Tuesday 6.45pm Beginner-Improver</span><span class="venue">The Parish Centre, Elm Rd, Fenbury</span></li>
      <li><span class="time">Wednesday 10am Progressive</span><span class="venue">The Parish Centre, Elm Rd, Fenbury</span></li>
      <li><span class="time">Wednesday 11am Beginners</span><span class="venue">The Parish Centre, Elm Rd, Fenbury</span></li>
      <li><span class="time">Wednesday 6.45pm Beginner-Progressive</span><span class="venue">The Community Hall, Broad St, Lynford Nr, Harwell</span></li>
      <li><span class="time">Thursday 10am Beginner-Progressive</span><span class="venue">Parochial Hall, High St, Ashvale</span></li>
      <li><span class="time">Thursday 6.30pm Progressive-</span><span class="venue">The Parish Centre, Mill Rd, Oakridge</span></li>
      <li><span class="time">Thursday 7.30pm Beginner-Progressive</span><span class="venue">The Parish Centre, Mill Rd, Oakridge</span></li>
    </ul>
    <div class="photo-circle photo-circle--a" role="img" aria-label="Photo of a class doing a side plank on mats"></div>
    <div class="photo-circle photo-circle--b" role="img" aria-label="Photo of a class exercising with pilates rings"></div>
  </div>

  <div class="panel panel--soft">
    <div class="layer">
      <h2 class="heading heading--about">About Maren</h2>
      <div class="about">
        <div class="portrait" role="img" aria-label="Portrait photo of the founder, Maren"></div>
        <p>Maren is one of the most experienced and leading Pilates teachers in the Midlands. She has been studying and working within the fitness industry for 20 years. Since 1992, she has specialized in aerobics, dance and other studio-based classes.</p>
        <p>In 1999, Maren received her first degree in Sport and Leisure from the University of Ashvale. In 2000, she became the studio aerobic and fitness programme coordinator for the largest sports centre in England</p>
        <p>2001 saw Maren study and complete a Diploma in Pilates with Daniel Brooke, London. In 2002, Maren established Harwell Core Pilates, which bases its teaching practice on the Pilates method and combines up to date knowledge of exercise physiology and techniques whilst retaining the authentic concept of the method's founder. For the past 15 years, Maren has taught Pilates locally, nationally and internationally.</p>
        <p>Since Maren 2006 Maren has continued with her professional development and studied Osteopathy, Traditional Acupuncture at Westmere University and Tai Chi.This wealth of knowledge and comprehensive skill-base brings a unique richness to her classes and private sessions.</p>
        <p>Maren is now works with a large professional network throughout the midlands and currently at team member of Linden Clinic and Ashvale Spine clinic, Harwellshire.</p>
      </div>
      <p class="call">CALL: 07700 900123</p>
      <p class="contact">hello@harwellcorepilates.co.uk<br>www.harwell-core-pilates.co.uk</p>
    </div>
    <div class="social">LIKE US AT <span class="social-square"></span></div>
  </div>

  <div class="panel panel--shaded">
    <div class="cover-photo" role="img" aria-label="Photo of a mixed group of men and women stretching sideways in a class"></div>
    <div class="brand layer">
      <div class="brand-mark"></div>
      <p class="brand-name">HARWELL CORE PILATES</p>
      <p class="brand-tag">Teaching Pilates Since 2001</p>
    </div>
    <p class="cover-line">Teaching pilates with a wealth of knowledge and experience for <span>over 15 of years</span></p>
  </div>
</section>

<!-- INSIDE SHEET -->
<section class="sheet sheet--inside">
  <svg class="wave wave--top" viewBox="0 0 790 180" preserveAspectRatio="none" aria-hidden="true">
    <defs>
      <linearGradient id="seaIn" x1="0" x2="1" y1="0" y2="0">
        <stop offset="0" stop-color="#33b8a4"/>
        <stop offset=".6" stop-color="#3aa7ad"/>
        <stop offset="1" stop-color="#3a9fb5"/>
      </linearGradient>
    </defs>
    <path d="M263,0 L790,0 L790,40 C690,70 560,100 430,120 C360,130 300,130 263,126 Z" fill="url(#seaIn)"/>
    <path d="M0,118 C90,106 180,128 263,136 C420,150 600,110 790,40 L790,70 C610,140 420,175 263,160 C180,152 90,130 0,134 Z" fill="#3277b5"/>
    <path d="M0,134 C90,130 180,152 263,160 C420,175 610,140 790,70 L790,88 C610,156 420,186 263,172 C180,166 90,146 0,148 Z" fill="#abd037"/>
  </svg>

  <div class="panel">
    <div class="roller-photo" role="img" aria-label="Photo of a woman doing a leg raise on a foam roller"></div>
    <div class="layer" style="margin-top:138px">
      <h2 class="heading heading--section">What is Pilates?</h2>
      <p class="body-text">Pilates is now the hottest and most talked about fitness trend since the aerobic explosion of the past 30 years. A perfect blend of Eastern and Western philosophy. Pilates is a holistic approach to exercise, that integrates body and mind. It concentrates on building strength, stamina, balance and co-ordination, thus improving flexibility, coordination, posture, breathing and well-being.</p>
      <h3 class="subhead">Classes</h3>
      <p class="body-text">All classes are based upon the original 34 movements developed by the method's founder. Classes provide low impact, yet highly intense workouts, ideal for everyone, whatever age or ability or whether the individual is fit, sedentary or recuperating after illness or surgery. Furthermore, Pilates provides a safe and beneficial workout for expectant and new mothers.</p>
      <p class="body-text" style="margin-top:4px">Each session is designed to,</p>
      <ul class="benefits">
        <li>Change the way you look</li>
        <li>Create lean muscles</li>
        <li>Increase strength, flexibility, coordination and proper body alignment</li>
        <li>Increase core strength</li>
        <li>Reduce fatigue, stress and risk of injury</li>
        <li>Reduce back and joint pain</li>
        <li>Rehabilitate</li>
        <li>Improve body mind integration</li>
      </ul>
    </div>
  </div>

  <div class="panel panel--soft" style="background:transparent">
    <div class="band-title">
      <p class="name">HARWELL CORE PILATES</p>
      <p class="phone">CALL: 07700 900123</p>
    </div>
    <div class="layer" style="margin-top:88px">
      <h2 class="heading heading--section">Class Description</h2>
      <h3 class="subhead">Small Group Pilates (new)</h3>
      <p class="body-text">This class structure is similar to a private session. Maximum of 6 people per class allows movement plans to be more tailored to an individual's needs than a larger class would. This programme will take you from the basics and help you to build on your skills to improve posture and to develop strength and flexibility. Home plan provided.</p>
      <h3 class="subhead">Beginner-Improvers</h3>
      <p class="body-text">Ideal for those who are new to the Pilates technique. In this programme, you will develop an understanding of the principals, gain strength, stamina and flexibility safely, as you are guided through a series of beginner movements, modified and tailored to your own needs and ability.</p>
      <h3 class="subhead">Beginner-Improvers</h3>
      <p class="body-text">Ideal stepping stone from a beginner class, building on moves that you have already learnt at a more intense level, as well as learning new moves. Incorporating small equipment such as the isotoner, the stability ball, roller and Pilates balance weights, to help increase the intensity of the workout without it being over challenging for those still developing their skill base.</p>
      <p class="web">www.harwell-core-pilates.co.uk</p>
    </div>
  </div>

  <div class="panel panel--shaded" style="background:linear-gradient(90deg,rgba(240,241,242,.6),#eceeef)">
    <div class="layer" style="margin-top:172px">
      <h3 class="subhead" style="margin-top:0">Intermediate-Advanced</h3>
      <p class="body-text">This class is designed for those already well versed in the Pilates technique. Both physically and mentally challenging, new movements are incorporated with combinations and higher intensity of known movements, alongside the use of small equipment.</p>
      <h2 class="heading heading--section" style="margin-top:10px">Private Sessions</h2>
      <p class="body-text">Perfect for anyone with specific needs, restricted time frame, or limited ability. Sessions are built using the 8 Pilates principals and designed to encompass all your individual needs, with the focus upon restoring strength, flexibility, equilibrium and well-being. Continued support and home movement plans are provided to help motivate and to help with achieving your goals.</p>
      <p class="body-text" style="margin-top:8px">Your private session can be arranged in the convenience of your own home, or a location near to you. Please contact Maren for further details and availability.</p>
    </div>
    <div class="group-photo" role="img" aria-label="Photo of a row of people doing side-lying leg lifts on mats"></div>
  </div>
</section>

</body>
</html>
```